Bramwell Specialty Coffee needs a Packaging design

We need packaging design for coffee that suits our brand identity, that is the best quality in Mexico.
We only sell mexican coffee with Q scores above 80
We are evaluating 3 types of packaging: Bag, Box and Cillinder can
The specific package format will be decided based on the designs that we get.

Target Market(s)

Coffee experts and enthusiast.
People that relate the Coffee consumption and experience with wine tasting and Bon Vivant way

Requirements
Should not have
• Photos any mexican cliché

```html
<!DOCTYPE html>
<html lang="en">
<head>
<meta charset="utf-8">
<title>Bramwell Specialty Coffee — Tube Packaging</title>
<link rel="stylesheet" href="https://fonts.googleapis.com/css2?family=Montserrat:wght@500&display=swap">
<style>
  :root {
    --page: #f7f6f4;
    --kraft: #b7aa90;
    --kraft-seam: #a59880;
    --label-paper: #f6f5f3;
    --roast-dark: #4a2c1c;
    --roast-medium: #6e4527;
    --roast-light: #9c6a3a;
    --roast-blonde: #b98a4e;
  }
  * { box-sizing: border-box; margin: 0; padding: 0; }
  html, body {
    width: 1200px;
    height: 1000px;
    overflow: hidden;
    background: var(--page);
  }
  .range {
    position: relative;
    width: 1200px;
    height: 1000px;
  }
  .tube {
    position: absolute;
    top: 230px;
    width: 268px;
    height: 595px;
    background: var(--kraft);
  }
  .tube__lid-seam {
    position: absolute;
    left: 0;
    right: 0;
    top: 132px;
    height: 2px;
    background: var(--kraft-seam);
  }
  .tube--dark   { left: 40px;  --roast: var(--roast-dark); }
  .tube--medium { left: 330px; --roast: var(--roast-medium); }
  .tube--light  { left: 622px; --roast: var(--roast-light); }
  .tube--blonde { left: 906px; --roast: var(--roast-blonde); }

  .label {
    position: absolute;
    top: -6px;
    left: 34px;
    width: 158px;
    height: 406px;
    border: 2px solid var(--roast);
    background: var(--label-paper);
  }
  .tube--medium .label { left: 46px; }
  .tube--light .label { left: 62px; }
  .tube--blonde .label { left: 76px; }

  .label__pattern {
    height: 96px;
    background: linear-gradient(160deg, var(--roast) 0%, color-mix(in srgb, var(--roast) 70%, #fff) 100%);
  }
  .label__panel {
    position: relative;
    height: 306px;
    border-top: 2px solid var(--roast);
  }
  .label__mark {
    position: absolute;
    top: 12px;
    left: 90px;
    font: 500 9px/1 "Montserrat", sans-serif;
    color: var(--roast);
  }
  .label__name,
  .label__descriptor {
    position: absolute;
    writing-mode: vertical-rl;
    transform: rotate(180deg);
    font-family: "Montserrat", sans-serif;
    font-weight: 500;
    color: var(--roast);
    white-space: nowrap;
  }
  .label__name {
    left: 50px;
    top: 28px;
    height: 260px;
    font-size: 46px;
    text-align: center;
    letter-spacing: 1px;
  }
  .label__descriptor {
    left: 122px;
    top: 40px;
    height: 236px;
    font-size: 10px;
    letter-spacing: 1.6px;
    display: flex;
    align-items: center;
    gap: 8px;
  }
  .label__descriptor::before,
  .label__descriptor::after {
    content: "";
    width: 1px;
    height: 22px;
    background: var(--roast);
  }
</style>
</head>
<body>
  <main class="range">
    <section class="tube tube--dark">
      <div class="tube__lid-seam"></div>
      <div class="label">
        <div class="label__pattern" role="img" aria-label="Swirling scroll ornament pattern in dark roast brown"></div>
        <div class="label__panel">
          <span class="label__mark">®</span>
          <span class="label__name">Bramwell</span>
          <span class="label__descriptor">SPECIALTY COFFEE</span>
        </div>
      </div>
    </section>

    <section class="tube tube--medium">
      <div class="tube__lid-seam"></div>
      <div class="label">
        <div class="label__pattern" role="img" aria-label="Swirling scroll ornament pattern in medium roast brown"></div>
        <div class="label__panel">
          <span class="label__mark">®</span>
          <span class="label__name">Bramwell</span>
          <span class="label__descriptor">SPECIALTY COFFEE</span>
        </div>
      </div>
    </section>

    <section class="tube tube--light">
      <div class="tube__lid-seam"></div>
      <div class="label">
        <div class="label__pattern" role="img" aria-label="Swirling scroll ornament pattern in light roast brown"></div>
        <div class="label__panel">
          <span class="label__mark">®</span>
          <span class="label__name">Bramwell</span>
          <span class="label__descriptor">SPECIALTY COFFEE</span>
        </div>
      </div>
    </section>

    <section class="tube tube--blonde">
      <div class="tube__lid-seam"></div>
      <div class="label">
        <div class="label__pattern" role="img" aria-label="Swirling scroll ornament pattern in golden blonde roast"></div>
        <div class="label__panel">
          <span class="label__mark">®</span>
          <span class="label__name">Bramwell</span>
          <span class="label__descriptor">SPECIALTY COFFEE</span>
        </div>
      </div>
    </section>
  </main>
</body>
</html>
```